Catalogue Design Project

We need a catalog design for a new private university called Redwell Institute Bayshore (see website www.rwi-bs.org). The catalog should be about 30 pages maximum and will include items such as General Information, Academic schedule, department descriptions, program descriptions, course descriptions, school policies, student services, admissions, San diego Lifestyle, etc.
I will provide the text but I need a professional design with regard to page layouts. I have provided some examples.
Ok, i posted the catalog content, just missing course descriptions.
Target Market(s)
Young Professionals, Foreign Students
Industry/Entity Type
University
Look and feel
Each slider illustrates characteristics of the customer's brand and the style your logo design should communicate.

```html
<!DOCTYPE html>
<html lang="en">
<head>
<meta charset="utf-8">
<title>Import/Export Business Certificate</title>
<link href="https://fonts.googleapis.com/css2?family=Carlito:wght@400;700&display=swap" rel="stylesheet">
<style>
  :root {
    --ink: #1f1f1f;
    --brand-blue: #2a5a8f;
    --rule-blue: #6f93bf;
    --paper: #ffffff;
    --footer-grey: #8a8a8a;
    --photo-warm: #d9c49a;
    --photo-light: #f2ead8;
  }
  html, body { margin: 0; padding: 0; overflow: hidden; background: var(--paper); }
  .page {
    position: relative;
    width: 927px;
    height: 1200px;
    overflow: hidden;
    background: var(--paper);
    font-family: "Carlito", "Calibri", sans-serif;
    color: var(--ink);
  }
  .brand-name {
    position: absolute; left: 60px; top: 40px;
    display: flex; align-items: center; gap: 10px;
    font-size: 20px; font-weight: 400; color: var(--brand-blue);
    white-space: nowrap;
  }
  .brand-name .mark {
    width: 18px; height: 18px; border-radius: 50%; background: var(--brand-blue);
  }
  .header-photo {
    position: absolute;
    left: 560px; top: 0;
    width: 367px; height: 102px;
    background: linear-gradient(90deg, rgba(255,255,255,1) 0%, var(--photo-light) 30%, var(--photo-warm) 70%, #c7ad7d 100%);
  }
  .header-rule { position: absolute; left: 0; top: 101px; width: 927px; height: 2px; background: var(--rule-blue); }
  .section-tab { position: absolute; left: 533px; top: 102px; width: 394px; height: 39px; }
  .section-tab svg { position: absolute; left: 0; top: 0; }
  .section-tab span {
    position: absolute; left: 40px; top: 3px;
    font-size: 30px; line-height: 34px; color: #fff; white-space: nowrap;
  }
  .content { position: absolute; left: 80px; width: 803px; top: 0; height: 1150px; }
  .title {
    position: absolute; left: 0; right: 0; top: 200px;
    margin: 0; text-align: center; font-size: 27px; line-height: 34px; font-weight: 700;
  }
  .body-text {
    margin: 0; font-size: 20.8px; line-height: 36.4px; text-align: justify;
  }
  .block { position: absolute; left: 0; right: 0; font-size: 20.8px; line-height: 36.4px; }
  .intro { position: absolute; left: 0; right: 0; top: 235px; }
  .topics { position: absolute; left: 0; right: 0; top: 417px; }
  .meta { top: 599px; }
  .meta b { font-weight: 700; }
  .label { text-decoration: underline; }
  .course { top: 708px; }
  .outcome { top: 817px; }
  .footer-rule { position: absolute; left: 0; top: 1156px; width: 927px; height: 2px; background: var(--rule-blue); }
  .folio {
    position: absolute; right: 36px; top: 1171px;
    font-size: 13px; color: var(--footer-grey); letter-spacing: 0.3px;
  }
</style>
</head>
<body>
<div class="page">
  <div class="brand-name"><span class="mark"></span><span>Redwell Institute Bayshore</span></div>

  <div class="header-photo" role="img" aria-label="Photo of an open old book fading into the header"></div>
  <div class="header-rule"></div>

  <div class="section-tab">
    <svg width="394" height="39" viewBox="0 0 394 39" aria-hidden="true">
      <polygon points="0,0 394,0 394,39 24,39" fill="var(--brand-blue)"/>
    </svg>
    <span>CERTIFICATE PROGRAMS</span>
  </div>

  <div class="content">
    <h1 class="title">Import/Export Business Certificate</h1>
    <p class="body-text intro">This course covers the exploration process of pursuing a business opportunity involving the purchase or selling of goods or even launching a career in the field of import/export.&nbsp; Students of the certificate program will learn to focus their energy on finding buyers, understanding what their interests are and negotiating a profitable way to meet their needs.</p>
    <p class="body-text topics">The certificate class will also include in-depth discussions of such topics as the functions of traffic management services performed by freight forwarders as utilized in shipping bulk products across multiple check points, the ever-changing of governmental restrictions and regulations, efficient port and trade routes, and completion of required documentation for the facilitation and coordination of moving goods domestically and internationally.</p>
    <div class="block meta">
      <div><b>Hours:</b> 6 hours per week</div>
      <div><b>Length:</b> 8 weeks per course</div>
    </div>
    <div class="block course">
      <div class="label">Course:</div>
      <div>BUS 602 Fundamentals of Importing &amp; Exporting</div>
    </div>
    <div class="block outcome">
      <div class="label">Learning Outcome:</div>
      <p class="body-text">Acquire in-depth knowledge of international markets, methods to locate buyers and sellers, and learn how to price, position, and sell a product or service to the right customer.</p>
    </div>
  </div>

  <div class="footer-rule"></div>
  <div class="folio">13::: REDWELL INSTITUTE</div>
</div>
</body>
</html>
```